The Velvet Rig

need a business card for a dj and sound equipment hire(rentals) business based in Melbourne. i have attached a current card get an idea. card needs to be unique professional looking.

ps.this card is not for a DJ. it's a rental business of dj equipment and pa systems.

Industry/Entity Type

Business

Font styles to use
Sans Serif
Script

Requirements
Must have
• Business Name: THE VELVET RIG
Contact Person: KIERAN MALLORY
Mobile: 047 VELVET 91
Email: KIERAN@THEVELVETRIG.COM.AU
Website: WWW.THEVELVETRIG.COM.AU
Pixelwall: WWW.PIXELWALL.CM/THEVELVETRIG.COM.AU

```html
<!DOCTYPE html>
<html lang="en">
<head>
<meta charset="utf-8">
<title>The Velvet Rig – Business Card</title>
<link rel="stylesheet" href="https://fonts.googleapis.com/css2?family=Cormorant+Garamond:wght@500;600&display=swap">
<style>
  :root {
    --page-bg: #dfe6e8;
    --card-black: #000000;
    --card-teal: #2f5058;
    --card-deep: #0a1214;
    --title-light: #f2fbff;
    --title-cyan: #5cc8ea;
    --band-blue: #3ec3e6;
    --ink: #000000;
    --mark-teal: #4a9aa6;
  }
  * { box-sizing: border-box; margin: 0; padding: 0; }
  html, body {
    width: 1200px;
    height: 1000px;
    overflow: hidden;
    background: var(--page-bg);
  }
  body {
    position: relative;
    font-family: "Cormorant Garamond", Georgia, serif;
  }
  .business-card {
    position: absolute;
    left: 80px;
    top: 190px;
    width: 1040px;
    height: 620px;
    border-radius: 26px;
    overflow: hidden;
    background: linear-gradient(180deg,
      var(--card-black) 0%,
      #070b0c 22%,
      var(--card-teal) 58%,
      #1c3036 68%,
      var(--card-deep) 100%);
  }
  .card-header {
    position: absolute;
    top: 22px;
    left: 0;
    width: 100%;
    text-align: center;
  }
  .brand-name,
  .contact-person {
    background: linear-gradient(180deg, var(--title-light) 15%, var(--title-cyan) 95%);
    -webkit-background-clip: text;
    background-clip: text;
    color: transparent;
    font-weight: 500;
  }
  .brand-name {
    font-size: 82px;
    line-height: 1;
    letter-spacing: 1px;
  }
  .contact-person {
    font-size: 42px;
    line-height: 1.1;
    letter-spacing: 0.5px;
  }
  .brand-mark {
    position: absolute;
    top: 228px;
    left: 0;
    width: 100%;
    display: flex;
    justify-content: center;
    align-items: center;
    gap: 22px;
  }
  .brand-mark-dot {
    width: 72px;
    height: 72px;
    border-radius: 50%;
    border: 8px solid var(--mark-teal);
  }
  .brand-mark-name {
    font-size: 64px;
    font-weight: 600;
    letter-spacing: 4px;
    color: var(--mark-teal);
  }
  .contact-band {
    position: absolute;
    left: 0;
    bottom: 0;
    width: 100%;
    height: 152px;
    background: var(--band-blue);
    padding-top: 10px;
    text-align: center;
    color: var(--ink);
  }
  .contact-line {
    font-size: 30px;
    font-weight: 500;
    line-height: 1.1;
    list-style: none;
  }
</style>
</head>
<body>
  <article class="business-card">
    <header class="card-header">
      <h1 class="brand-name">The Velvet Rig</h1>
      <p class="contact-person">Kieran Mallory</p>
    </header>

    <div class="brand-mark">
      <span class="brand-mark-dot"></span>
      <span class="brand-mark-name">THE VELVET RIG</span>
    </div>

    <ul class="contact-band">
      <li class="contact-line">Mobile : 047 VELVET 91</li>
      <li class="contact-line">Website : www.THEVELVETRIG.com.au</li>
      <li class="contact-line">Email : KIERAN@THEVELVETRIG.com.au</li>
      <li class="contact-line">Pixelwall: www.pixelwall.cm/THEVELVETRIG</li>
    </ul>
  </article>
</body>
</html>
```